Business Card Design Project

Looking for a logo and business card for a Real State Business i will be opening. The name is not choosen yet , but will probably be RWT IMOVEIS.
I was thinking black and silver colors, but am open to nice ideas.
I did add a business card that i liked a lot, am looking for something like that, with logo in black or silver in a black card. The logo i was thinking in the letters RWT as i uploaded or something or little and cute buildings or a house...just ideas, can be any nice logo.
Updates

You guys can add other colors if you want, I like colors very "BRIGHT" and "open", like red, pink, strong colors. almost glow in the dark colors. lol

Designers,

I've increased more 88 dollars in the budget for 1st place cause I will want envelope designs... small and big sizes.

So 1st place is now U$248,00. 

No need to send the envelope designs right now... only the business cards designs.

Thank you.

Industry/Entity Type

Business

Requirements
Must have
• Marcela Tavares Rocha

www.RWTimoveis-exemplo.com.br

+554187316042

marcela@rwtimoveis-exemplo.com.br

```html
<!DOCTYPE html>
<html lang="pt-BR">
<head>
<meta charset="utf-8">
<title>RWT Imoveis – Business Card</title>
<link href="https://fonts.googleapis.com/css2?family=Josefin+Sans:wght@300;400;700&display=swap" rel="stylesheet">
<style>
  :root {
    --stage: #4a4a4c;
    --card-dark: #2b2a2b;
    --skyline-dark: #3b3a3c;
    --brand-pink: #ec008c;
    --skyline-pink: #f2379f;
    --ink: #2b2a2b;
    --white: #ffffff;
  }
  * { margin: 0; padding: 0; box-sizing: border-box; }
  html, body {
    width: 1200px; height: 892px; overflow: hidden;
    background: var(--stage);
    font-family: "Josefin Sans", sans-serif;
  }
  .canvas { position: relative; width: 1200px; height: 892px; }

  .card {
    position: absolute; width: 640px; height: 392px; overflow: hidden;
    box-shadow: 0 8px 22px rgba(0,0,0,0.45);
  }
  .skyline {
    position: absolute; left: 0; right: 0; bottom: 0; height: 120px;
  }

  /* Front */
  .card-front { left: 412px; top: 72px; background: var(--card-dark); }
  .card-front .skyline {
    background: linear-gradient(to bottom, rgba(59,58,60,0) 0%, var(--skyline-dark) 45%);
  }
  .brand-block {
    position: absolute; left: 170px; top: 52px; width: 360px;
    text-align: center; z-index: 1;
  }
  .brand-name {
    color: var(--brand-pink); font-weight: 700; font-size: 150px;
    line-height: 1; letter-spacing: -2px;
  }
  .brand-sub {
    color: var(--white); font-weight: 700; font-size: 76px;
    line-height: 1; margin-top: -8px; letter-spacing: 1px;
  }
  .brand-tagline {
    color: var(--brand-pink); font-weight: 300; font-size: 38px;
    line-height: 1; margin-top: 4px;
  }

  /* Back */
  .card-back { left: 114px; top: 424px; background: var(--brand-pink); }
  .card-back .skyline {
    height: 140px;
    background: linear-gradient(to bottom, rgba(242,55,159,0) 0%, var(--skyline-pink) 40%);
  }
  .back-mark {
    position: absolute; left: 150px; top: 80px; width: 120px; height: 170px;
    display: flex; align-items: center; justify-content: center;
    color: var(--ink); font-weight: 700; font-size: 56px;
  }
  .contact {
    position: absolute; left: 288px; top: 84px; z-index: 1;
  }
  .contact-name { color: var(--ink); font-weight: 700; font-size: 19px; }
  .contact-role { color: var(--white); font-weight: 400; font-size: 17px; margin-top: 4px; }
  .contact-list { list-style: none; margin-top: 26px; }
  .contact-list li {
    display: flex; align-items: center; gap: 10px;
    color: var(--white); font-size: 19px; font-weight: 300; line-height: 1.25;
  }
  .contact-list svg { width: 14px; height: 14px; fill: var(--ink); flex: none; }
  .contact-web { color: var(--white); font-size: 22px; font-weight: 400; margin-top: 4px; }
</style>
</head>
<body>
<main class="canvas">

  <section class="card card-front">
    <div class="brand-block">
      <div class="brand-name">RWT</div>
      <div class="brand-sub">IMOVEIS</div>
      <div class="brand-tagline">Real Estate Agent</div>
    </div>
    <div class="skyline" role="img" aria-label="City skyline silhouette in dark grey"></div>
  </section>

  <section class="card card-back">
    <div class="back-mark">RWT</div>
    <div class="contact">
      <div class="contact-name">Marcela Tavares Rocha</div>
      <div class="contact-role">Real Estate Agent</div>
      <ul class="contact-list">
        <li>
          <svg viewBox="0 0 16 16" aria-hidden="true"><path d="M2 6c0-2 3-3 6-3s6 1 6 3v1h-3V6H5v1H2zM4 8h8l2 6H2z"/></svg>
          +55 4187 316 042
        </li>
        <li>
          <svg viewBox="0 0 16 16" aria-hidden="true"><path d="M1 4h14v9H1z M1 4l7 5 7-5" stroke="#ec008c" stroke-width="1"/></svg>
          marcela@rwtimoveis-exemplo.com.br
        </li>
      </ul>
      <div class="contact-web">www.RWTimoveis-exemplo.com.br</div>
    </div>
    <div class="skyline" role="img" aria-label="City skyline silhouette in light pink"></div>
  </section>

</main>
</body>
</html>
```